Electrician Letterhead Design MVR

We need some letterhead for our bills and other papers.
Customer address is on the right side (Swiss format)
A4 format

Design should also be applicable on Cards

Target Market(s)

Private Customers, Small Business

Industry/Entity Type

Electrician

Other font styles liked:
• incised 901

Colors
00AB8E
00BBA5
67D7C9
C6EFE9
E9F9F6

```html
<!DOCTYPE html>
<html lang="en">
<head>
<meta charset="utf-8">
<title>MVR Letterhead</title>
<link rel="stylesheet" href="https://fonts.googleapis.com/css2?family=Arimo:wght@400;700&family=Mulish:wght@700;800&display=swap">
<style>
  :root {
    --teal: #00A08A;
    --teal-light: #00BBA5;
    --ink: #111111;
    --text: #4a4a4a;
    --paper: #ffffff;
    --backdrop: #dcdcdc;
  }
  * { margin: 0; padding: 0; box-sizing: border-box; }
  html, body {
    width: 1189px;
    height: 1200px;
    overflow: hidden;
    background: var(--backdrop);
  }
  .sheet {
    position: absolute;
    left: 191px;
    top: 30px;
    width: 806px;
    height: 1140px;
    background: var(--paper);
    font-family: "Arimo", Arial, sans-serif;
    color: var(--text);
  }
  .brand {
    position: absolute;
    left: 70px;
    top: 40px;
    font-family: "Mulish", sans-serif;
    font-weight: 800;
    font-size: 82px;
    line-height: 1;
    letter-spacing: 2px;
    color: var(--teal);
  }
  .rule-band {
    position: absolute;
    left: 0;
    top: 123px;
    width: 100%;
    height: 6px;
    background: var(--teal);
  }
  .rule-thin {
    position: absolute;
    left: 0;
    top: 135px;
    width: 100%;
    height: 2px;
    background: var(--ink);
  }
  .tagline {
    position: absolute;
    left: 64px;
    top: 118px;
    padding: 0 6px;
    background: var(--paper);
    font-family: "Mulish", sans-serif;
    font-weight: 700;
    font-size: 12px;
    line-height: 16px;
    letter-spacing: 0.4px;
    color: var(--ink);
    white-space: nowrap;
  }
  .address {
    position: absolute;
    right: 220px;
    top: 60px;
    text-align: right;
    font-style: normal;
    font-size: 13px;
    line-height: 16px;
  }
  .divider {
    position: absolute;
    left: 599px;
    top: 63px;
    width: 1px;
    height: 43px;
    background: var(--text);
  }
  .contact {
    position: absolute;
    left: 611px;
    top: 60px;
    list-style: none;
    font-size: 13px;
    line-height: 16px;
  }
  .contact li { display: flex; align-items: center; gap: 8px; white-space: nowrap; }
  .contact svg { width: 10px; height: 10px; flex: none; }
  .salutation {
    position: absolute;
    left: 73px;
    top: 350px;
    font-family: "Mulish", sans-serif;
    font-weight: 700;
    font-size: 19px;
    color: var(--text);
  }
  .letter-body {
    position: absolute;
    left: 72px;
    top: 403px;
    font-size: 13.9px;
    line-height: 16.5px;
  }
  .letter-body p + p { margin-top: 15px; }
  .letter-body .line { display: block; white-space: nowrap; }
  .closing {
    position: absolute;
    left: 73px;
    top: 745px;
    font-family: "Mulish", sans-serif;
    font-weight: 700;
    font-size: 10.5px;
  }
  .signature {
    position: absolute;
    left: 73px;
    top: 795px;
    width: 132px;
    height: 38px;
    background: linear-gradient(90deg, #e6e6e6, #f3f3f3);
  }
</style>
</head>
<body>
  <main class="sheet">
    <header class="letterhead">
      <div class="brand">MVR</div>
      <div class="rule-band"></div>
      <div class="rule-thin"></div>
      <div class="tagline">Elektrotechnik Voltara GmbH</div>

      <address class="address">
        Your address<br>city<br>state, ZIP 0000
      </address>
      <div class="divider"></div>
      <ul class="contact">
        <li>
          <svg viewBox="0 0 10 10" aria-hidden="true"><path d="M2 1 L4 1 L4.6 3 L3.4 3.8 Q4.3 5.8 6.2 6.6 L7 5.4 L9 6 L9 8 Q8.5 9 7.5 9 Q1 8 1 2.5 Q1 1.5 2 1 Z" fill="var(--teal)"/></svg>
          555-018-4297
        </li>
        <li>
          <svg viewBox="0 0 10 10" aria-hidden="true"><rect x="0.5" y="2" width="9" height="6" fill="var(--teal)"/><path d="M0.5 2 L5 5.5 L9.5 2" fill="none" stroke="#fff" stroke-width="0.9"/></svg>
          youremail@mailbox.com
        </li>
        <li>
          <svg viewBox="0 0 10 10" aria-hidden="true"><circle cx="5" cy="5" r="4.3" fill="var(--teal)"/><path d="M0.8 5 H9.2 M5 0.8 Q2.5 5 5 9.2 M5 0.8 Q7.5 5 5 9.2" fill="none" stroke="#fff" stroke-width="0.7"/></svg>
          www.yourwebsite.com
        </li>
      </ul>
    </header>

    <h1 class="salutation">Dear Mr. Smith,</h1>

    <section class="letter-body">
      <p>
        <span class="line">Lorem ipsum dolor sit amet, consectetuer adipiscing elit, sed diam nonmmy nibh euismod tincidunt ut laor</span>
        <span class="line">eet dolore magna aliquam erat volutpat. Ut wisi enim ad minim veniam, quis nostrud exerci tationmcorper</span>
        <span class="line">suscipit lobortis nisl ut aliquip ex ea commodo consequat. Duis autem vel eum iriure dolor in hendrerit in</span>
        <span class="line">vulputate velit esse molestie consequat, vel illum dolore eu feugiat</span>
      </p>
      <p>
        <span class="line">Rorem ipsum dolor sit amet, consectetuer adipiscing elit, sed diam nonmmy nibh euismod tincidunt ut laor</span>
        <span class="line">eet dolore magna aliquam erat volutpat. Ut wisi enim ad minim veniam, quis nostrud exerci tationmcorper</span>
        <span class="line">suscipit lobortis nisl ut aliquip ex ea commodo consequat. Duis autem vel eum iriure dolor in hendrerit in</span>
        <span class="line">vulputate velit esse molest</span>
      </p>
      <p>
        <span class="line">Dorem ipsum dolor sit amet, consectetuer adipiscing elit, sed diam nonmmy nibh euismod tincidunt ut laor</span>
        <span class="line">eet dolore magna aliquam erat volutpat. Ut wisi enim ad minim veniam, quis nostrud exerci tationmcorper</span>
        <span class="line">suscipit lobortis nisl ut aliquip ex ea commodo consequat. Duis autem vel eum iriure dolor in hendrerit in</span>
        <span class="line">suscipit lobortis nisl ut aliquip ex ea commodo consequat. Duis autem vel eum iriure dolor in hendrerit in</span>
        <span class="line">vulputate velit esse molestie consequat, vel illum</span>
      </p>
      <p>
        <span class="line">Sorem ipsum dolor sit amet, consectetuer adipiscing elit, sed diam nonmmy nibh euismod tincidunt ut laor</span>
        <span class="line">eet dolore magna aliquam erat volutpat. Ut wisi enim ad minim veniam, quis nostrud exerci tationmcorper</span>
        <span class="line">suscipit lobortis nisl ut aliquip ex ea commodo consequat. Duis autem vel eum iriure dolor in</span>
      </p>
    </section>

    <p class="closing">Sincerely,</p>
    <div class="signature" role="img" aria-label="Handwritten signature of the sender"></div>
  </main>
</body>
</html>
```